Field Trace Studies: Abductions

Book cover. Casebound and Perfect bound. Size 5.5 x 8.5 (portrait). Approx 165 pages for spine. Will be using Quillmark PressForge for printer so be sure to follow those specifications. This is a textbook for Search & Rescue and Law Enforcement search planners on deciding where they should look for someone who has been abducted. Nothing morbid. It will be a book in a series. The series is called Field Trace Studies. That should be in smaller letters at the top. Abductions should be the major title feature. The series will have a border on the front cover of safety orange (255, 121, 0) for RGB. vkM logo on front, spine, and back. Place holder for ISBN, author bio, book description, endorsements on back.

Target Market(s)

Professional textbook for Law Enforcement, Search and Rescue, Academic (criminologist)

Industry/Entity Type

Search and Rescue - Law Enforcement. Major colors for industry is orange for SAR and blue for Law enforcement

Requirements
Must have
• Safety Orange border (0.25 inch), vkM Logos, small Field Trace Studies title on top, large Abductions title. Author's name (Daniel P. Wrenfield)
Nice to have
• Not sure if picture or illustration works best. Topographic map is possible, law enforcement and searcher working together, clandestine grave, dirt road, all possible
Should not have
• no dead bodies, no bones, no skulls, no urban environment

```html
<!DOCTYPE html>
<html lang="en">
<head>
<meta charset="utf-8">
<title>Abductions — Field Trace Studies — Cover Wrap</title>
<link rel="stylesheet" href="https://fonts.googleapis.com/css2?family=Bebas+Neue&family=Arimo:wght@400&family=Open+Sans:wght@400;600&display=swap">
<style>
  :root {
    --safety-orange: #ff7900;
    --border-orange: #f0600c;
    --navy: #2a3158;
    --navy-mid: #3a4370;
    --navy-deep: #131935;
    --ink-white: #f2f3f7;
    --paper: #f4f4f4;
    --label-grey: #e4e4e4;
    --label-text: #9a9a9a;
  }
  * { margin: 0; padding: 0; box-sizing: border-box; }
  html, body { width: 1200px; height: 960px; overflow: hidden; background: var(--paper); }

  .cover-wrap {
    position: absolute; left: 40px; top: 86px;
    width: 1120px; height: 788px;
  }

  /* ---------- Back cover ---------- */
  .back-cover {
    position: absolute; left: 0; top: 0; width: 518px; height: 788px;
    background: var(--border-orange);
  }
  .back-panel {
    position: absolute; inset: 14px;
    background: var(--navy);
    overflow: hidden;
  }
  .back-ridge-top, .back-ridge-bottom {
    position: absolute; left: 0; right: 0;
  }
  .back-ridge-top {
    top: 0; height: 96px;
    background: linear-gradient(180deg, var(--navy-deep) 0%, var(--navy-deep) 55%, var(--navy) 100%);
  }
  .back-ridge-bottom {
    bottom: 0; height: 100px;
    background: linear-gradient(0deg, var(--navy-deep) 0%, var(--navy-deep) 40%, var(--navy) 100%);
  }
  .author-photo {
    position: absolute; left: 29px; top: 100px; width: 115px; height: 147px;
    background: var(--label-grey);
  }
  .back-title {
    position: absolute; left: 160px; top: 96px;
    font-family: "Bebas Neue", sans-serif; font-size: 40px; line-height: 1;
    color: var(--ink-white); letter-spacing: 0.5px;
  }
  .back-series {
    position: absolute; left: 161px; top: 135px;
    font-family: "Arimo", sans-serif; font-size: 12px; color: var(--ink-white);
    text-transform: uppercase;
  }
  .back-copy {
    font-family: "Arimo", sans-serif; font-size: 11.5px; line-height: 15.2px;
    color: var(--ink-white); text-align: justify;
  }
  .back-copy p { margin-bottom: 15px; }
  .copy-lead {
    position: absolute; left: 160px; top: 154px; width: 302px;
  }
  .copy-body {
    position: absolute; left: 21px; top: 263px; width: 447px;
  }
  .bio-heading { display: block; }

  .logo-tile {
    position: absolute; background: #ffffff;
    display: flex; align-items: center; justify-content: center;
  }
  .logo-name {
    font-family: "Arimo", sans-serif; font-weight: 400; color: var(--navy-deep);
  }
  .back-logo { left: 29px; top: 665px; width: 86px; height: 68px; }
  .back-logo .logo-name { font-size: 34px; }

  .isbn-label {
    position: absolute; left: 291px; top: 654px; width: 170px; height: 85px;
    background: var(--label-grey);
    display: flex; align-items: center; justify-content: center;
    font-family: "Open Sans", sans-serif; font-size: 24px; letter-spacing: 8px;
    color: var(--label-text);
  }

  /* ---------- Spine ---------- */
  .spine {
    position: absolute; left: 518px; top: 0; width: 84px; height: 788px;
    background: linear-gradient(90deg, var(--navy) 0%, var(--navy-mid) 55%, var(--navy) 100%);
  }
  .spine-title, .spine-author {
    position: absolute; left: 50%; white-space: nowrap;
    transform-origin: 0 0; color: var(--ink-white);
  }
  .spine-title {
    top: 30px; transform: rotate(90deg) translateY(-50%);
    font-family: "Bebas Neue", sans-serif; font-size: 38px; line-height: 1;
  }
  .spine-author {
    top: 342px; transform: rotate(90deg) translateY(-50%);
    font-family: "Open Sans", sans-serif; font-size: 19px; letter-spacing: 9px;
  }
  .spine-logo { left: 14px; top: 708px; width: 56px; height: 66px; }
  .spine-logo .logo-name {
    font-size: 26px; transform: rotate(90deg); display: inline-block;
  }

  /* ---------- Front cover ---------- */
  .front-cover {
    position: absolute; left: 602px; top: 0; width: 518px; height: 788px;
    background: var(--border-orange);
  }
  .front-panel {
    position: absolute; inset: 14px;
    background: linear-gradient(180deg, var(--navy-deep) 0%, var(--navy-deep) 8%, var(--navy-mid) 16%, var(--navy) 55%, var(--navy-deep) 100%);
    overflow: hidden;
  }
  .front-series {
    position: absolute; left: 0; right: 0; top: 156px;
    display: flex; align-items: center; justify-content: center; gap: 12px;
    font-family: "Open Sans", sans-serif; font-size: 14px; color: var(--ink-white);
    text-transform: uppercase;
  }
  .series-rule { width: 72px; height: 1px; background: var(--ink-white); }
  .front-title {
    position: absolute; left: 0; right: 0; top: 174px; text-align: center;
    font-family: "Bebas Neue", sans-serif; font-size: 112px; line-height: 1;
    color: var(--safety-orange); letter-spacing: 1px;
  }
  .front-subtitle {
    position: absolute; left: 0; right: 0; top: 286px; text-align: center;
    font-family: "Open Sans", sans-serif; font-size: 14px; line-height: 18px;
    color: var(--ink-white); text-transform: uppercase;
  }
  .field-scene {
    position: absolute; left: 0; right: 0; top: 362px; height: 290px;
    background: radial-gradient(ellipse at 45% 45%, #4a5484 0%, var(--navy-mid) 30%, #1d2446 75%, var(--navy-deep) 100%);
  }
  .front-author {
    position: absolute; left: 0; right: 0; top: 700px; text-align: center;
    font-family: "Open Sans", sans-serif; font-size: 22px; letter-spacing: 4px;
    color: var(--ink-white);
  }
</style>
</head>
<body>
  <main class="cover-wrap">

    <section class="back-cover">
      <div class="back-panel">
        <div class="back-ridge-top" role="img" aria-label="Dark mountain ridge silhouette along the top edge"></div>
        <div class="back-ridge-bottom" role="img" aria-label="Dark hill silhouette along the bottom edge"></div>

        <div class="author-photo" role="img" aria-label="Author photo placeholder"></div>
        <h2 class="back-title">ABDUCTIONS</h2>
        <p class="back-series">Field Trace Studies</p>

        <div class="back-copy copy-lead">
          <p>When a person is taken against their will, every decision made in the first hours can determine the outcome. Abductions delivers a structured, evidence-based approach for search planners, law enforcement professionals, and rescue teams tasked with locating abducted individuals.</p>
        </div>

        <div class="back-copy copy-body">
          <p>Drawing from real-world case analysis, behavioral patterns, and search theory, this book bridges the gap between investigation and field operations. It provides actionable insights into offender behavior, victim movement, and geographic profiling allowing teams to prioritize search areas with greater precision and efficiency.</p>
          <p>Designed as part of the Field Trace Studies series, this volume integrates proven methodologies with practical tools to support coordinated response efforts. Whether operating in rural terrain or complex environments, professionals will gain a clearer understanding of where to search, why those locations matter, and how to allocate resources effectively.</p>
          <p>This is not speculation—it is a disciplined framework built for those responsible for bringing people home.</p>
          <p><span class="bio-heading">About the Author</span>Daniel P. Wrenfield is a recognized authority in search and rescue planning, with decades of experience analyzing lost person incidents and developing behavior-based search strategies used worldwide.</p>
        </div>

        <div class="logo-tile back-logo"><span class="logo-name">vkM</span></div>
        <div class="isbn-label">ISBN</div>
      </div>
    </section>

    <section class="spine">
      <span class="spine-title">ABDUCTIONS</span>
      <span class="spine-author">WRENFIELD</span>
      <div class="logo-tile spine-logo"><span class="logo-name">vkM</span></div>
    </section>

    <section class="front-cover">
      <div class="front-panel">
        <p class="front-series"><span class="series-rule"></span>Field Trace Studies<span class="series-rule"></span></p>
        <h1 class="front-title">ABDUCTIONS</h1>
        <p class="front-subtitle">Search &amp; Rescue and Law Enforcement<br>Planning Guide</p>
        <div class="field-scene" role="img" aria-label="Silhouette of a police officer with a flashlight and a searcher examining disturbed ground among tall grass at night"></div>
        <p class="front-author">Daniel P. Wrenfield</p>
      </div>
    </section>

  </main>
</body>
</html>
```